Letterhead for a German Distribution/Manufacturing Company

We need a professional Letterhead in a unique Design.
not to playful.
The Letterhead has to show show that we are a international company with headquater in Nordmark.
all details like adress, Vat Tax Number, Bank Accout, Eori, email, Company number has to be on the Letterhead.
for example use: VAT TAX DE5470318 Bank Account: Kestrel Bank IBAN DE412058731ß204683 Swift: MORV0417352 EORI 3150428697 Company Number: HRB 51806 Adress: VOLMINTA UG Ahornweg 7 Postal Code 06384 City Lindenbrück Country: Nordmark Email: info@volminta-example.com
the design can be colored but doesnt have to be
Industry/Entity Type
Manufacturing and international distribution
Requirements
Must have
- show that we are a international company with headquater in Nordmark. our company infos and logo

```html
<!DOCTYPE html>
<html lang="en">
<head>
<meta charset="utf-8">
<title>VOLMINTA Letterhead</title>
<link rel="stylesheet" href="https://fonts.googleapis.com/css2?family=Barlow:wght@400;500&family=Jost:wght@400;500;600;700&display=swap">
<style>
  :root {
    --backdrop: #e4e4e4;
    --paper: #ffffff;
    --ink: #2b2b2b;
    --ink-soft: #3a3a3a;
    --band: #3d3d3d;
    --rule: #8a8a8a;
  }
  * { box-sizing: border-box; margin: 0; padding: 0; }
  html, body { width: 1200px; height: 1200px; overflow: hidden; }
  body { background: var(--backdrop); position: relative; }

  .letterhead {
    position: absolute; left: 197px; top: 30px;
    width: 806px; height: 1140px;
    background: var(--paper);
    color: var(--ink);
    box-shadow: 0 2px 10px rgba(0,0,0,0.08);
  }

  .brand {
    position: absolute; left: 78px; top: 128px;
    display: flex; align-items: center; gap: 14px;
  }
  .brand-dot { width: 34px; height: 34px; border-radius: 50%; background: var(--ink-soft); }
  .brand-name {
    font-family: "Jost", sans-serif; font-weight: 500;
    font-size: 40px; letter-spacing: 1px; color: var(--ink-soft);
  }

  .sender {
    position: absolute; left: 560px; top: 66px;
    font-family: "Jost", sans-serif; font-size: 11.5px; line-height: 15px;
    font-style: normal; color: var(--ink);
  }
  .sender .email { display: flex; align-items: center; gap: 6px; margin-left: 10px; }
  .sender svg { width: 11px; height: 9px; }

  .recipient {
    position: absolute; left: 118px; top: 290px;
    font-family: "Barlow", sans-serif; font-size: 15px; line-height: 19px;
    letter-spacing: 0.6px; color: var(--ink);
  }

  .salutation {
    position: absolute; left: 150px; top: 402px;
    font-family: "Barlow", sans-serif; font-size: 14px; letter-spacing: 0.6px;
  }

  .body-copy {
    position: absolute; left: 150px; top: 440px; width: 620px;
    font-family: "Barlow", sans-serif; font-size: 13.5px; line-height: 23px;
    letter-spacing: 0.5px; color: var(--ink);
  }
  .body-copy span { display: block; white-space: nowrap; }

  .signature {
    position: absolute; left: 240px; top: 800px;
    width: 220px; height: 58px; border-radius: 4px;
    background: linear-gradient(90deg, #efefef, #f7f7f7);
  }
  .closing {
    position: absolute; left: 240px; top: 866px;
    font-family: "Barlow", sans-serif; font-size: 14px; letter-spacing: 0.6px;
  }

  .footer-details {
    position: absolute; left: 70px; top: 1036px; right: 40px;
    display: flex; font-family: "Jost", sans-serif; font-size: 12.5px;
    line-height: 16px; color: var(--ink);
  }
  .footer-details .col { width: 230px; padding: 0 18px; }
  .footer-details .col + .col { border-left: 1px solid var(--rule); }
  .footer-details strong { font-weight: 700; }

  .footer-band {
    position: absolute; left: 0; right: 0; bottom: 0; height: 14px;
    display: flex; gap: 4px;
  }
  .footer-band .segment { background: var(--band); flex: 1; }
  .footer-band .segment.first { flex: 0 0 300px; }
  .footer-band .segment.middle { flex: 0 0 240px; }
</style>
</head>
<body>
  <main class="letterhead">
    <div class="brand">
      <div class="brand-dot"></div>
      <div class="brand-name">VOLMINTA</div>
    </div>

    <address class="sender">
      <div>VOLMINTA UG Ahornweg 7</div>
      <div>Postal Code 06384</div>
      <div>City Lindenbrück Country: Nordmark</div>
      <div class="email">
        <svg viewBox="0 0 11 9" aria-hidden="true"><rect x="0.5" y="0.5" width="10" height="8" fill="none" stroke="#2b2b2b"/><path d="M0.5 0.5 L5.5 5 L10.5 0.5" fill="none" stroke="#2b2b2b"/></svg>
        info@volminta-example.com
      </div>
    </address>

    <div class="recipient">
      <div>Mr. John Doe</div>
      <div>President</div>
      <div>Strategy Accountants</div>
      <div>111 Street Name,</div>
      <div>City State, 12345</div>
    </div>

    <div class="salutation">Dear :</div>

    <p class="body-copy">
      <span>Lorem ipsum dolor sit amet, consectetur adipiscing elit. Aenean ut ipsum eget massa hendrerit</span>
      <span>vestibulum vel in velit. Donec pretium neque velit.</span>
      <span>Aliquam porta lectus nec mauris ornare venenatis. Vivamus non est turpis, et cursus sem. Mauris</span>
      <span>vehicula erat in diam auctor at bibendum nisl lacinia.</span>
      <span>Morbi imperdiet neque vehicula nunc convallis gravida. Vestibulum iaculis pretium placerat. Integer</span>
      <span>consequat, est sit amet facilisis eleifend, nibh nibh varius orci, eget dapibus arcu dui non purus.</span>
      <span>Pellentesque in magna mauris. Duis enim sapien, dictum vitae condimentum a, pulvinar vel lacus.</span>
      <span>Mauris et molestie nibh. Vestibulum vitae nulla at metus elementum porta sit amet interdum elit.</span>
      <span>Nulla sollicitudin neque eu nulla volutpat congue.</span>
      <span>Etiam pellentesque, velit id dapibus fermentum, turpis sapien ornare dui, ac tincidunt ligula odio</span>
      <span>congue purus. Nunc sed ante dui, in porta lectus. Cras nec sem lorem. In hac habitasse platea</span>
      <span>dictumst. Maecenas id diam quis dui porta tristique. Sed id egestas felis. Donec ullamcorper mattis</span>
      <span>posuere. Phasellus fermentum eleifend tortor vel dapibus. Vestibulum ante ipsum.</span>
    </p>

    <div class="signature" role="img" aria-label="Handwritten signature of the sender"></div>
    <div class="closing">Sincerely,</div>

    <footer class="footer-details">
      <div class="col">
        <div><strong>VAT TAX</strong> DE5470318</div>
        <div><strong>Swift:</strong> MORV0417352</div>
      </div>
      <div class="col">
        <div><strong>Bank Account:</strong> Kestrel Bank</div>
        <div><strong>EORI</strong> 3150428697</div>
      </div>
      <div class="col">
        <div><strong>IBAN</strong> DE412058731ß204683</div>
        <div><strong>Company Number:</strong> HRB 51806</div>
      </div>
    </footer>

    <div class="footer-band">
      <div class="segment first"></div>
      <div class="segment middle"></div>
      <div class="segment"></div>
    </div>
  </main>
</body>
</html>
```